Home Security Company Business Card

Looking for a eye catching business card that is non traditional and stands out but yet still looks professional. It should include all the pertinent information such as name, title, address, telephone, e-mail, website address should definitely stand out and then finally the logo.

Target Market(s)

Residential and Commercial accounts mostly upscale accounts

Industry/Entity Type

Security

Contact Information for Business Card

Name
Title
Address
Office #
Cell #
E-mail
Website

Font styles to use
Serif
Sans Serif

Requirements
Must have
• Logo, two sided color configuration
Nice to have
• You decide
Should not have
• There really aren't any.

```html
<!DOCTYPE html>
<html lang="en">
<head>
<meta charset="utf-8">
<title>Bulwark Home Protection – Business Card</title>
<link rel="stylesheet" href="https://fonts.googleapis.com/css2?family=Cinzel:wght@400&family=Open+Sans:wght@400;600;700&display=swap">
<style>
  :root {
    --maroon: #7a1c2a;
    --maroon-dark: #5e1320;
    --gold: #e9b949;
    --gold-soft: #f3cf6e;
    --paper: #ffffff;
    --stage: #ece8e2;
    --ink-shadow: rgba(40, 20, 10, 0.18);
  }
  * { box-sizing: border-box; margin: 0; padding: 0; }
  html, body { width: 1200px; height: 913px; overflow: hidden; }
  body {
    background: var(--stage);
    font-family: "Open Sans", Arial, sans-serif;
    display: flex;
    align-items: center;
    justify-content: center;
    gap: 40px;
  }
  .card {
    position: relative;
    width: 540px;
    height: 309px;
    background: var(--paper);
    box-shadow: 0 6px 18px var(--ink-shadow);
    overflow: hidden;
  }
  .card__bands { position: absolute; inset: 0; }
  .brand {
    position: absolute;
    display: flex;
    align-items: center;
    gap: 10px;
    font-family: "Cinzel", Georgia, serif;
    font-weight: 400;
    color: var(--maroon);
    line-height: 1.1;
  }
  .brand__dot {
    flex: none;
    border-radius: 50%;
    background: var(--gold);
  }
  /* front */
  .card--front .brand { top: 34px; left: 290px; font-size: 17px; }
  .card--front .brand__dot { width: 34px; height: 34px; }
  .rule {
    position: absolute;
    left: 0; top: 168px;
    width: 270px; height: 1px;
    background: var(--maroon);
  }
  .person { position: absolute; left: 28px; top: 180px; }
  .person__name {
    font-size: 22px; font-weight: 700; color: var(--maroon-dark);
  }
  .person__title {
    position: absolute; left: 148px; top: -14px;
    font-size: 12px; color: var(--gold);
  }
  .person__address {
    margin-top: 2px; font-size: 13.5px; line-height: 1.3; color: var(--maroon);
  }
  .contacts {
    position: absolute; left: 282px; top: 142px;
    list-style: none; font-size: 12.5px; color: var(--maroon); line-height: 1.45;
  }
  .contacts li { display: flex; align-items: center; gap: 8px; }
  .contacts svg { width: 11px; height: 11px; flex: none; }
  /* back */
  .card--back .brand {
    top: 100px; left: 50%; transform: translateX(-50%);
    font-size: 22px; white-space: nowrap;
  }
  .card--back .brand__dot { width: 46px; height: 46px; }
  .website {
    position: absolute; left: 0; right: 0; top: 218px;
    text-align: center; font-size: 16px; font-weight: 700; color: var(--maroon);
  }
</style>
</head>
<body>

  <section class="card card--front" aria-label="Business card front">
    <svg class="card__bands" viewBox="0 0 540 309" aria-hidden="true">
      <polygon points="330,222 540,222 540,250 315,250" fill="var(--gold-soft)"/>
      <polygon points="140,309 300,309 320,262 160,262" fill="var(--maroon)"/>
      <circle cx="318" cy="252" r="7" fill="var(--gold)"/>
    </svg>
    <div class="brand">
      <span class="brand__dot"></span>
      <span>Bulwark<br>Home Protection Inc.</span>
    </div>
    <div class="rule"></div>
    <div class="person">
      <span class="person__title">Owner</span>
      <h1 class="person__name">Daniel Hartwell</h1>
      <p class="person__address">742 Maple Avenue<br>Fairview, Ohio 44126</p>
    </div>
    <ul class="contacts">
      <li>
        <svg viewBox="0 0 12 12"><rect x="1" y="4" width="10" height="7" rx="1.5" fill="none" stroke="var(--gold)" stroke-width="1.4"/><path d="M2 4 Q6 0 10 4" fill="none" stroke="var(--gold)" stroke-width="1.4"/></svg>
        +330 5550-1234
      </li>
      <li>
        <svg viewBox="0 0 12 12"><path d="M3 1 L5 4 L4 5 Q5 7.5 7 8 L8 7 L11 9 L9.5 11 Q2 10 1 2.5 Z" fill="var(--gold)"/></svg>
        +3305550-48213
      </li>
      <li>
        <svg viewBox="0 0 12 12"><rect x="1" y="2.5" width="10" height="7" fill="none" stroke="var(--gold)" stroke-width="1.4"/><path d="M1 2.5 L6 7 L11 2.5" fill="none" stroke="var(--gold)" stroke-width="1.4"/></svg>
        info@danielhartwellmail.com
      </li>
    </ul>
  </section>

  <section class="card card--back" aria-label="Business card back">
    <div class="brand">
      <span class="brand__dot"></span>
      <span>Bulwark<br>Home Protection Inc.</span>
    </div>
    <p class="website">www.bulwarkhomeprotectioninc.com</p>
  </section>

</body>
</html>
```